Acupuncture business needs business card design

I need a business card for an acupuncture clinic called "Harbourlight Wellness"
It will need the following details:
My name: Marcus Pelling
Acupuncturist
Member TVBH
KWF Treatment Provider
Ph numbers: 581 2734 027 418 5620
Email: marcus@hbwel.example.nz
On the back it will need a table with 2 columns for appointments, one column for time and one for date.

Industry/Entity Type

Clinic

Contact Information for Business Card

Marcus Pelling
Acupuncturist
Member TVBH
KWF Treatment Provider
Email: marcus@hbwel.example.nz

Requirements
Must have
• Marcus Pelling
• Acupuncturist
• Member TVBH
• KWF Treatment Provider
• Ph numbers: 581 2734 027 418 5620
• Email: marcus@hbwel.example.nz
• On the back it will need a table with 2 columns for appointments, one column for time and one for date.

```html
<!DOCTYPE html>
<html lang="en">
<head>
<meta charset="utf-8">
<title>Harbourlight Wellness – Business Card</title>
<link rel="stylesheet" href="https://fonts.googleapis.com/css2?family=Raleway:wght@400;500;600&display=swap">
<style>
  :root {
    --page: #ebe7e0;
    --card: #ffffff;
    --blue: #1c9fdc;
    --rule: #c9e6f5;
    --ink: #4a4a4a;
    --ink-soft: #6e6e6e;
    --tag: #555555;
    --shade: #e6e6e6;
  }
  * { box-sizing: border-box; margin: 0; padding: 0; }
  html, body { width: 1057px; height: 1200px; overflow: hidden; }
  body {
    background: var(--page);
    font-family: "Raleway", sans-serif;
    color: var(--ink);
    position: relative;
  }
  .card {
    position: absolute;
    top: 197px;
    width: 460px;
    height: 805px;
    background: var(--card);
    box-shadow: 0 6px 18px rgba(0,0,0,.18);
    overflow: hidden;
  }
  .card--front { left: 45px; }
  .card--back { left: 552px; }

  .wordmark { display: flex; align-items: center; gap: 16px; }
  .wordmark__square { width: 18px; height: 18px; background: var(--blue); flex: none; }
  .wordmark__name {
    font-weight: 500;
    color: var(--ink);
    letter-spacing: 4px;
    line-height: 1.25;
    text-transform: uppercase;
  }

  /* front: brand + appointment table */
  .card--front .wordmark {
    position: absolute;
    left: 0; right: 0; top: 70px;
    justify-content: center;
  }
  .card--front .wordmark__name { font-size: 26px; }
  .appointments {
    position: absolute;
    left: 40px; right: 40px; top: 190px;
  }
  .appointments__title {
    font-size: 13px;
    font-weight: 600;
    letter-spacing: 3px;
    color: var(--blue);
    text-transform: uppercase;
    margin-bottom: 12px;
  }
  .appointments table {
    width: 100%;
    border-collapse: collapse;
    table-layout: fixed;
  }
  .appointments th {
    background: var(--blue);
    color: #fff;
    font-size: 13px;
    font-weight: 600;
    letter-spacing: 2px;
    text-align: left;
    padding: 9px 14px;
  }
  .appointments td {
    height: 40px;
    border-bottom: 1px solid var(--rule);
    border-right: 1px solid var(--rule);
  }
  .appointments td:last-child { border-right: 0; }
  .front-shade {
    position: absolute;
    left: 0; right: 0; top: 548px;
    height: 22px;
    background: linear-gradient(var(--card), var(--shade));
  }
  .front-band {
    position: absolute;
    left: 0; right: 0; top: 570px;
    height: 96px;
    background: var(--blue);
    display: flex; align-items: center; justify-content: center;
  }
  .front-band__web { color: #fff; font-size: 17px; letter-spacing: 3px; }

  /* back: person + contact */
  .name-tag {
    position: absolute;
    left: 0; top: 70px;
    width: 270px; height: 52px;
    background: var(--tag);
    color: #fff;
    font-size: 21px;
    font-weight: 500;
    letter-spacing: 3px;
    display: flex; align-items: center;
    padding-left: 34px;
  }
  .role {
    position: absolute;
    left: 34px; top: 136px;
  }
  .role__title {
    font-size: 14px;
    font-weight: 600;
    letter-spacing: 2px;
    color: var(--ink);
    text-transform: uppercase;
  }
  .role__credential {
    margin-top: 8px;
    font-size: 13px;
    letter-spacing: 1px;
    color: var(--ink-soft);
  }
  .role__credential + .role__credential { margin-top: 4px; }
  .card--back .wordmark { position: absolute; left: 34px; top: 290px; }
  .card--back .wordmark__name { font-size: 24px; }
  .back-band {
    position: absolute;
    left: 0; right: 0; top: 430px;
    height: 170px;
    background: var(--blue);
    display: grid;
    grid-template-columns: 1fr 1.35fr;
    align-content: center;
    row-gap: 22px;
    padding: 0 26px 0 34px;
  }
  .contact {
    display: flex; align-items: center; gap: 10px;
    color: #fff;
    font-size: 14px;
    letter-spacing: .5px;
    white-space: nowrap;
  }
  .icon {
    width: 24px; height: 24px;
    background: #fff;
    border-radius: 4px;
    flex: none;
    display: flex; align-items: center; justify-content: center;
  }
  .icon svg { width: 16px; height: 16px; fill: var(--blue); }
  .address { position: absolute; left: 34px; top: 640px; color: var(--ink); }
  .address .icon { background: var(--blue); }
  .address .icon svg { fill: #fff; }
</style>
</head>
<body>

<section class="card card--front" aria-label="Business card front">
  <div class="wordmark">
    <span class="wordmark__square"></span>
    <span class="wordmark__name">Harbourlight<br>Wellness</span>
  </div>
  <div class="appointments">
    <p class="appointments__title">Your next appointment</p>
    <table>
      <thead><tr><th>Date</th><th>Time</th></tr></thead>
      <tbody>
        <tr><td></td><td></td></tr>
        <tr><td></td><td></td></tr>
        <tr><td></td><td></td></tr>
        <tr><td></td><td></td></tr>
        <tr><td></td><td></td></tr>
        <tr><td></td><td></td></tr>
      </tbody>
    </table>
  </div>
  <div class="front-shade"></div>
  <div class="front-band">
    <span class="front-band__web">www.hbwel.example.nz</span>
  </div>
</section>

<section class="card card--back" aria-label="Business card back">
  <div class="name-tag">MARCUS PELLING</div>
  <div class="role">
    <p class="role__title">Acupuncturist</p>
    <p class="role__credential">Member TVBH</p>
    <p class="role__credential">KWF Treatment Provider</p>
  </div>

  <div class="wordmark">
    <span class="wordmark__square"></span>
    <span class="wordmark__name">Harbourlight<br>Wellness</span>
  </div>

  <div class="back-band">
    <div class="contact">
      <span class="icon"><svg viewBox="0 0 24 24"><path d="M6.6 10.8a15 15 0 0 0 6.6 6.6l2.2-2.2a1 1 0 0 1 1-.25 11.4 11.4 0 0 0 3.6.57 1 1 0 0 1 1 1V20a1 1 0 0 1-1 1A17 17 0 0 1 3 4a1 1 0 0 1 1-1h3.5a1 1 0 0 1 1 1c0 1.25.2 2.45.57 3.57a1 1 0 0 1-.25 1z"/></svg></span>
      581 2734
    </div>
    <div class="contact">
      <span class="icon"><svg viewBox="0 0 24 24"><path d="M3 5h18v14H3z M3 5l9 7 9-7" fill="none" stroke="#1c9fdc" stroke-width="2"/></svg></span>
      marcus@hbwel.example.nz
    </div>
    <div class="contact">
      <span class="icon"><svg viewBox="0 0 24 24"><path d="M6.6 10.8a15 15 0 0 0 6.6 6.6l2.2-2.2a1 1 0 0 1 1-.25 11.4 11.4 0 0 0 3.6.57 1 1 0 0 1 1 1V20a1 1 0 0 1-1 1A17 17 0 0 1 3 4a1 1 0 0 1 1-1h3.5a1 1 0 0 1 1 1c0 1.25.2 2.45.57 3.57a1 1 0 0 1-.25 1z"/></svg></span>
      027 418 5620
    </div>
    <div class="contact">
      <span class="icon"><svg viewBox="0 0 24 24"><circle cx="12" cy="12" r="9" fill="none" stroke="#1c9fdc" stroke-width="2"/><path d="M3 12h18M12 3c3 3 3 15 0 18M12 3c-3 3-3 15 0 18" fill="none" stroke="#1c9fdc" stroke-width="1.6"/></svg></span>
      www.hbwel.example.nz
    </div>
  </div>

  <div class="contact address">
    <span class="icon"><svg viewBox="0 0 24 24"><path d="M12 2a7 7 0 0 0-7 7c0 5.2 7 13 7 13s7-7.8 7-13a7 7 0 0 0-7-7zm0 9.5A2.5 2.5 0 1 1 12 6.5a2.5 2.5 0 0 1 0 5z"/></svg></span>
    14 Quay Road, Level 3, Harbour St
  </div>
</section>

</body>
</html>
```